Quillbrook IT company focused on 3 areas of IT

Looking for something similar to attached cards. Logo for quillbrook also attached.. Looking for something clean as far as colors (surprise me).. Quill stands for 3 primary areas, web design, consulting and network infrastructure design. Please email me if you have any questions. Looking forward to seeing how creative and professional this card will look. Thank you,

Target Market(s)

Small business/consumers looking for It services

Industry/Entity Type

It Service

Contact Information for Business Card

Dorin Vasek
Principal Consultant

202-555-0173

www.quillbrook-example.com
dvasek@quillbrook-example.com

27416 Copper Lantern Way,
Germantown, MD 20999

Colors

Designer to choose colors to be used in the design.

Requirements
Must have
• attached Logo design. Feel free to play with the colors.. If you have a better idea for a card, please fee free to send me. Looking for something clean/modern. Should have tech feel, not cheesy.
Nice to have
• Surprise me :-)..

```html
<!DOCTYPE html>
<html lang="en">
<head>
<meta charset="utf-8">
<title>Quillbrook Business Card</title>
<link href="https://fonts.googleapis.com/css2?family=Lato:wght@400;700;900&display=swap" rel="stylesheet">
<style>
  :root {
    --backdrop: #1c1c1c;
    --card-black: #0d0d0d;
    --card-white: #ffffff;
    --ink: #1f2a2e;
    --ink-soft: #2f3a3e;
    --silver: #c9c9c9;
    --map-tint: #d6e6f3;
    --rule: #1f2a2e;
  }
  * { box-sizing: border-box; margin: 0; padding: 0; }
  html, body {
    width: 1200px;
    height: 900px;
    overflow: hidden;
    background: var(--backdrop);
    font-family: "Lato", sans-serif;
  }
  .canvas {
    position: relative;
    width: 1200px;
    height: 900px;
  }
  .card {
    position: absolute;
    width: 630px;
    height: 360px;
    border-radius: 18px;
    overflow: hidden;
  }

  /* Front: black side */
  .card-front {
    left: 190px;
    top: 70px;
    background: var(--card-black);
    box-shadow: 0 0 0 1px #2a2a2a;
  }
  .card-front .brand {
    position: absolute;
    left: 0; right: 0;
    top: 128px;
    text-align: center;
    display: flex;
    justify-content: center;
    align-items: center;
    gap: 14px;
  }
  .card-front .brand-mark {
    width: 22px; height: 22px;
    background: var(--silver);
  }
  .card-front .brand-name {
    font-weight: 900;
    font-size: 44px;
    letter-spacing: 2px;
    color: var(--silver);
  }
  .card-front .website {
    position: absolute;
    left: 0; right: 0;
    bottom: 44px;
    text-align: center;
    font-weight: 700;
    font-size: 14px;
    letter-spacing: 5px;
    color: #ffffff;
  }

  /* Back: white side */
  .card-back {
    left: 380px;
    top: 470px;
    background: var(--card-white);
    box-shadow: 0 0 0 1px #dcdcdc;
    color: var(--ink);
  }
  .world-map {
    position: absolute;
    left: 120px;
    top: 40px;
    width: 470px;
    height: 260px;
    border-radius: 40px;
    background: radial-gradient(ellipse at center, var(--map-tint) 0%, rgba(214,230,243,0.55) 60%, rgba(214,230,243,0) 100%);
  }
  .card-back .brand {
    position: absolute;
    left: 0; right: 0;
    top: 62px;
    display: flex;
    justify-content: center;
    align-items: center;
    gap: 12px;
  }
  .card-back .brand-mark {
    width: 18px; height: 18px;
    background: var(--ink);
  }
  .card-back .brand-name {
    font-weight: 900;
    font-size: 36px;
    letter-spacing: 1.5px;
    color: var(--ink);
  }
  .divider {
    position: absolute;
    left: 236px;
    right: 30px;
    top: 206px;
    height: 2px;
    background: var(--rule);
  }
  .address {
    position: absolute;
    right: 30px;
    top: 218px;
    text-align: right;
    font-weight: 700;
    font-size: 13px;
    line-height: 1.4;
    color: var(--ink);
  }
  .person {
    position: absolute;
    left: 30px;
    top: 192px;
  }
  .person-name {
    font-size: 19px;
    font-weight: 400;
    color: var(--ink);
  }
  .person-name strong { font-weight: 900; }
  .person-title {
    font-size: 13px;
    color: var(--ink-soft);
    margin-top: 2px;
  }
  .contacts {
    position: absolute;
    left: 30px;
    top: 262px;
    list-style: none;
    font-size: 14px;
    color: var(--ink);
  }
  .contacts li {
    display: flex;
    align-items: center;
    gap: 10px;
    margin-bottom: 8px;
  }
  .contacts svg { width: 14px; height: 14px; fill: var(--ink); flex: none; }
</style>
</head>
<body>
<main class="canvas">

  <section class="card card-front" aria-label="Card front">
    <div class="brand">
      <span class="brand-mark"></span>
      <span class="brand-name">Quillbrook</span>
    </div>
    <p class="website">www.quillbrook-example.com</p>
  </section>

  <section class="card card-back" aria-label="Card back">
    <div class="world-map" role="img" aria-label="Faint dotted world map in light blue"></div>

    <div class="brand">
      <span class="brand-mark"></span>
      <span class="brand-name">Quillbrook</span>
    </div>

    <div class="divider"></div>

    <address class="address" style="font-style: normal;">
      27416 Copper Lantern Way,<br>
      Germantown, MD 20999
    </address>

    <div class="person">
      <p class="person-name">Dorin <strong>Vasek</strong></p>
      <p class="person-title">Chief Executive Offer</p>
    </div>

    <ul class="contacts">
      <li>
        <svg viewBox="0 0 24 24" aria-hidden="true"><path d="M6.6 10.8a15.1 15.1 0 0 0 6.6 6.6l2.2-2.2a1 1 0 0 1 1-.25 11.4 11.4 0 0 0 3.6.57 1 1 0 0 1 1 1V20a1 1 0 0 1-1 1A17 17 0 0 1 3 4a1 1 0 0 1 1-1h3.5a1 1 0 0 1 1 1c0 1.25.2 2.45.57 3.6a1 1 0 0 1-.25 1z"/></svg>
        <span>202-555-0173</span>
      </li>
      <li>
        <svg viewBox="0 0 24 24" aria-hidden="true"><path d="M2 5h20v14H2z M4 7v.5l8 5 8-5V7l-8 5z" fill-rule="evenodd"/></svg>
        <span>dvasek@quillbrook-example.com</span>
      </li>
    </ul>
  </section>

</main>
</body>
</html>
```